QVR business card

Need a business card for a company that provides instructional design and elearning development services. The website is here: http://quorvane.studio/

I'm attaching a current logo, as well as the old business card design. While I like to keep it clean, the old design is too simplistic for my liking. The only idea I want to reuse from the old design is placing industry jargon on the back of the card, just need a better way to present it. But if you have other ideas for the back--feel free to experiment.

Please use the colors complementary to the color we have on the website. Thank you!

```html
<!DOCTYPE html>
<html lang="en">
<head>
<meta charset="utf-8">
<title>QVR Business Card</title>
<link rel="stylesheet" href="https://fonts.googleapis.com/css2?family=Open+Sans:wght@400;600;700&display=swap">
<style>
  :root {
    --stage: #ececea;
    --paper: #ffffff;
    --teal: #0ab2af;
    --teal-mid: #5cc2b4;
    --sand: #dcd593;
    --gold: #d3c98c;
    --ink-light: #ffffff;
  }
  * { box-sizing: border-box; margin: 0; padding: 0; }
  html, body {
    width: 1200px; height: 900px; overflow: hidden;
    background: var(--stage);
    font-family: "Open Sans", Arial, sans-serif;
  }
  .canvas { position: relative; width: 1200px; height: 900px; }

  .card {
    position: absolute;
    background: var(--paper);
    box-shadow: 0 6px 18px rgba(0,0,0,0.18);
    overflow: hidden;
  }
  .card--front { left: 77px; top: 34px; width: 589px; height: 364px; }
  .card--back  { left: 388px; top: 505px; width: 567px; height: 352px; }

  .brand {
    position: absolute;
    display: flex; align-items: center; gap: 16px;
  }
  .card--front .brand { left: 40px; top: 58px; }
  .card--back .brand  { left: 38px; top: 30px; }
  .brand__dot {
    width: 46px; height: 46px; border-radius: 50%;
    background: var(--teal);
  }
  .brand__name {
    font-weight: 700; font-size: 56px; line-height: 1;
    color: var(--gold); letter-spacing: 2px;
  }

  .band {
    position: absolute; left: 0; right: 0; bottom: 0;
    background: linear-gradient(180deg, var(--teal) 0%, var(--teal) 22%, var(--teal-mid) 60%, var(--sand) 100%);
    color: var(--ink-light);
  }
  .card--front .band { top: 182px; }
  .card--back .band  { top: 128px; }

  .holder-name {
    position: absolute; left: 32px; top: 24px;
    font-size: 19px; font-weight: 600;
  }
  .contact-list {
    position: absolute; left: 32px; top: 86px;
    list-style: none;
  }
  .contact-list li {
    display: flex; align-items: center; gap: 8px;
    font-size: 15px; line-height: 21px;
  }
  .contact-list svg { width: 11px; height: 11px; fill: var(--ink-light); flex: none; }

  .services__title {
    position: absolute; left: 28px; top: 10px;
    font-size: 21px; font-weight: 600; letter-spacing: 0.3px;
  }
  .services__list {
    position: absolute; left: 28px; top: 40px;
    list-style: none;
  }
  .services__list li {
    display: flex; align-items: center; gap: 14px;
    font-size: 15px; font-weight: 600; line-height: 30px;
  }
  .services__list li::before {
    content: ""; width: 8px; height: 8px; border-radius: 50%;
    background: var(--ink-light); margin-left: 4px;
  }
</style>
</head>
<body>
<main class="canvas">

  <section class="card card--front" aria-label="Business card front">
    <div class="brand">
      <span class="brand__dot"></span>
      <span class="brand__name">QVR</span>
    </div>
    <div class="band">
      <p class="holder-name">Marten Holloway</p>
      <ul class="contact-list">
        <li>
          <svg viewBox="0 0 24 24" aria-hidden="true"><path d="M6.6 10.8a15.1 15.1 0 0 0 6.6 6.6l2.2-2.2c.3-.3.7-.4 1-.2 1.1.4 2.3.6 3.6.6.6 0 1 .4 1 1V20c0 .6-.4 1-1 1C10.6 21 3 13.4 3 4c0-.6.4-1 1-1h3.5c.6 0 1 .4 1 1 0 1.3.2 2.5.6 3.6.1.3 0 .7-.2 1z"/></svg>
          555-014-2273
        </li>
        <li>
          <svg viewBox="0 0 24 24" aria-hidden="true"><path d="M2 5h20v14H2z M3 6l9 7 9-7" /></svg>
          mholloway@quorvane.studio
        </li>
        <li>
          <svg viewBox="0 0 24 24" aria-hidden="true"><circle cx="12" cy="12" r="10"/></svg>
          www.quorvane.studio
        </li>
      </ul>
    </div>
  </section>

  <section class="card card--back" aria-label="Business card back">
    <div class="brand">
      <span class="brand__dot"></span>
      <span class="brand__name">QVR</span>
    </div>
    <div class="band services">
      <h2 class="services__title">HOW CAN WE HELP?</h2>
      <ul class="services__list">
        <li>Mobile Learning Scorm</li>
        <li>Instructional Design Lms</li>
        <li>Moocs Elearning Html5</li>
        <li>Adult Learning Theory</li>
        <li>Gamification Classroom</li>
        <li>Xapi Blended Learning</li>
      </ul>
    </div>
  </section>

</main>
</body>
</html>
```